web page design with coding

We are a start up insurance agency who needs to design a full functional web page. we recently did a postcard design though drawkettle I will upload the final project for you to see the color scheme/font we would like to continue to use. I also have a rough draft of verbage I would like our website to have. I will upload that as well.

Reason: I am sorry but the person who will make the final decision on the website is out of the country at the moment and will make the final decision when he returns.

Industry/Entity Type

Insurance

Coding

Coded - Design and coding required

```html
<!DOCTYPE html>
<html lang="en">
<head>
<meta charset="utf-8">
<title>Corvina Insurance Group</title>
<link href="https://fonts.googleapis.com/css2?family=Raleway:ital,wght@0,400;0,500;0,600;0,700;0,800;1,500&display=swap" rel="stylesheet">
<style>
:root{
  --navy:#1c3c6e;
  --green:#2e7d3e;
  --green-light:#3d8f4a;
  --orange:#f7a400;
  --orange-dark:#f08c00;
  --dark:#333333;
  --btn:#3b3b3b;
  --grey-bg:#f0f0f0;
  --text:#555555;
  --white:#ffffff;
}
*{box-sizing:border-box;margin:0;padding:0}
html,body{width:1200px;height:2586px;overflow:hidden}
body{position:relative;background:var(--white);font-family:"Raleway",Arial,sans-serif;color:var(--text)}
.abs{position:absolute}

/* hero */
.hero-photo{left:0;top:0;width:1200px;height:620px;
  background:linear-gradient(180deg,#7fb9e6 0%,#b9dbf3 40%,#d9e9f2 60%,#8cc05a 85%,#5c9a3a 100%)}
.hero-curve{left:0;top:480px;width:1200px;height:240px}
.logo{left:76px;top:31px;width:153px;height:93px;display:flex;align-items:center;justify-content:center;
  font-size:30px;font-weight:800;color:var(--navy);letter-spacing:1px}
.social{display:flex;gap:8px}
.social span{width:30px;height:30px;border-radius:50%;background:var(--navy);display:block}
.social.top{left:698px;top:32px}
.call{left:902px;top:20px;color:var(--navy)}
.call small{display:block;font-size:15px;font-weight:700;letter-spacing:.5px}
.call strong{display:block;font-size:29px;font-weight:700;color:var(--green);margin-top:-2px}
.nav{left:271px;top:92px;display:flex;align-items:center;height:32px}
.nav a{font-size:13px;font-weight:700;color:var(--navy);text-decoration:none;text-transform:uppercase;position:absolute;white-space:nowrap;line-height:32px}
.nav a.active{background:var(--navy);color:var(--white);padding:0 12px}
.hero-title{left:76px;top:218px;font-size:43px;line-height:50px;font-weight:800;color:var(--navy);text-transform:uppercase}
.btn-orange{background:linear-gradient(180deg,var(--orange),var(--orange-dark));color:var(--white);font-weight:700;text-transform:uppercase;display:flex;align-items:center;justify-content:center}
.hero-btn{left:76px;top:388px;width:241px;height:50px;font-size:17px}
.dots{left:76px;top:462px;display:flex;gap:8px}
.dots span{width:13px;height:13px;border-radius:50%;background:var(--white)}
.dots span:first-child{background:var(--navy)}
.badge{left:1036px;top:500px;width:90px;height:90px;border-radius:50%;background:#1d1d1d}

/* common */
.section-title{font-size:23px;font-weight:700;color:var(--navy);text-transform:uppercase}
.copy{font-size:15px;line-height:23.5px;color:var(--text)}
.btn-dark{background:var(--btn);color:var(--white);font-size:14px;font-weight:700;text-transform:uppercase;display:flex;align-items:center;justify-content:center;width:140px;height:43px;border-radius:2px}

/* welcome */
.welcome-photo{left:76px;top:800px;width:690px;height:198px;
  background:linear-gradient(90deg,#6c9a45 0%,#c9b79c 35%,#e6d3bf 55%,#7ea64e 80%,#4f7e33 100%)}
.quote-box{left:793px;top:759px;width:333px;height:455px;background:var(--green);border-radius:6px;padding:0 26px;color:var(--white)}
.quote-box h3{font-size:23px;font-weight:700;text-transform:uppercase;padding-top:24px;padding-bottom:8px;border-bottom:1px solid rgba(255,255,255,.25)}
.quote-box .ssl{font-size:14px;margin-top:20px;display:flex;align-items:center;gap:6px}
.field{height:40px;background:var(--white);border-radius:2px;margin-top:13px;font-size:14px;color:#888;padding:0 14px;display:flex;align-items:center}
.ssl + .field{margin-top:19px}
.quote-box .label{font-size:14px;margin-top:22px}
.radio{font-size:14px;display:flex;align-items:center;gap:10px;margin-top:12px}
.radio i{width:14px;height:14px;border-radius:50%;background:var(--white);display:block}
.quote-btn{height:43px;margin-top:24px;font-size:17px;border-radius:2px}

/* about */
.grey-band{left:0;top:1262px;width:1200px;height:497px;background:var(--grey-bg)}
.tagline{left:76px;top:1518px;font-size:16px;font-style:italic;font-weight:500;color:var(--green)}
.agent-card{left:795px;top:1350px;width:329px;height:284px;background:var(--white);border:1px solid #e2e2e2;box-shadow:0 10px 12px -8px rgba(0,0,0,.25);text-align:center}
.agent-photo{position:absolute;left:96px;top:17px;width:136px;height:136px;background:linear-gradient(180deg,#d8d8d8,#9aa3ad);border:6px solid var(--white);box-shadow:0 2px 6px rgba(0,0,0,.35);transform:rotate(-4deg)}
.agent-name{position:absolute;left:0;width:100%;top:170px;font-size:17px;font-weight:700;color:var(--green)}
.agent-role{position:absolute;left:0;width:100%;top:194px;font-size:12px;font-style:italic;color:var(--navy)}
.agent-desc{position:absolute;left:40px;width:249px;top:220px;font-size:15px;line-height:24px;color:var(--text)}
.mission{left:76px;top:1686px;width:1050px;height:145px;background:var(--green);text-align:center;color:var(--white);box-shadow:0 16px 14px -12px rgba(0,0,0,.3)}
.mission h2{font-size:23px;font-weight:700;text-transform:uppercase;margin-top:24px}
.mission p{font-size:16px;font-style:italic;font-weight:500;line-height:26px;margin-top:10px}

/* products */
.tile{top:1896px;width:293px;height:233px;display:flex;align-items:center;justify-content:center;text-align:center;color:var(--white);font-size:23px;font-weight:800;line-height:29px;text-transform:uppercase}
.tile-bg{position:absolute;inset:0}
.tile span{position:relative}
.tile.business .tile-bg{background:radial-gradient(circle at 50% 45%,#9fc37a,#4f7f32 80%)}
.tile.personal .tile-bg{background:radial-gradient(circle at 50% 45%,#a8c987,#517f38 80%)}

/* footer */
.footer-curve{left:0;top:2160px;width:1200px;height:112px}
.footer{left:0;top:2270px;width:1200px;height:316px;background:var(--dark)}
.f-logo{left:76px;top:2370px;width:110px;height:66px;display:flex;align-items:center;font-size:24px;font-weight:800;color:var(--white)}
.f-copy{left:76px;top:2456px;font-size:12px;line-height:18px;color:#cfcfcf}
.social.bottom{left:76px;top:2512px}
.social.bottom span{width:28px;height:28px;background:#666}
.f-col{top:2368px;color:#cfcfcf;font-size:13px;line-height:26px}
.f-col h4{font-size:13px;font-weight:700;color:var(--white);text-transform:uppercase;margin-bottom:4px}
.f-col .brand{color:#5fae5a}
.f-input{left:884px;top:2400px;width:242px;height:40px;background:var(--white);border-radius:2px;font-size:14px;color:#333;display:flex;align-items:center;padding:0 12px}
.f-btn{left:1050px;top:2457px;width:76px;height:36px;background:var(--green);color:var(--white);font-size:13px;font-weight:700;display:flex;align-items:center;justify-content:center;border-radius:2px}
</style>
</head>
<body>

<!-- hero -->
<div class="abs hero-photo" role="img" aria-label="Photo of a smiling family outdoors in front of a house under a blue sky"></div>
<svg class="abs hero-curve" viewBox="0 0 1200 240" aria-hidden="true">
  <path d="M0 10 C400 150 900 140 1200 70 L1200 240 L0 240 Z" fill="#2e7d3e"/>
  <path d="M0 60 C400 190 900 180 1200 110 L1200 240 L0 240 Z" fill="#ffffff"/>
  <path d="M30 105 C400 205 850 240 1200 130 L1200 150 C850 262 400 235 30 105 Z" fill="#1c3c6e"/>
</svg>
<div class="abs badge" aria-hidden="true"></div>

<header>
  <div class="abs logo">CORVINA</div>
  <div class="abs social top" aria-label="Social links"><span></span><span></span><span></span><span></span></div>
  <div class="abs call"><small>CALL US TODAY:</small><strong>(555) 010-4477</strong></div>
  <nav class="abs nav">
    <a class="active" style="left:0">Home</a>
    <a style="left:101px">About Us</a>
    <a style="left:222px">Products and Services</a>
    <a style="left:455px">Our Mission</a>
    <a style="left:598px">Request Quote</a>
    <a style="left:765px">Contact Us</a>
  </nav>
</header>

<h1 class="abs hero-title">We specialize in<br>commercial business &amp;<br>personal insurance</h1>
<div class="abs btn-orange hero-btn">Request Quote</div>
<div class="abs dots"><span></span><span></span><span></span><span></span></div>

<!-- welcome -->
<h2 class="abs section-title" style="left:76px;top:754px">Welcome to our website</h2>
<div class="abs welcome-photo" role="img" aria-label="Photo of a family relaxing together on the grass"></div>
<p class="abs copy" style="left:76px;top:1010px;width:690px">Corvina Insurance Group has joined with regional &amp; national insurance companies to provide quality products and superior service. We take the time to discuss options and coverages, not to just sell insurance products. We strive to educate you in the decision making process to become an informed consumer.<br>We specialize in commercial business &amp; personal insurance. We are committed to providing personal attention to all your insurance needs.</p>
<div class="abs btn-dark" style="left:76px;top:1169px">Read More</div>

<aside class="abs quote-box">
  <h3>Insurance Quote</h3>
  <div class="ssl"><svg width="11" height="13" viewBox="0 0 11 13"><rect x="0" y="5" width="11" height="8" rx="1" fill="#fff"/><path d="M2.5 5 V3.5 a3 3 0 0 1 6 0 V5" stroke="#fff" stroke-width="1.6" fill="none"/></svg>Secure 256-bit SSL Encryption</div>
  <div class="field">Name</div>
  <div class="field">Email Address</div>
  <div class="field">Phone No.</div>
  <div class="label">Select types of insurance</div>
  <div class="radio"><i></i>Business Insurance</div>
  <div class="radio"><i></i>Personal Insurance</div>
  <div class="btn-orange quote-btn">Got to Step 2</div>
</aside>

<!-- about -->
<div class="abs grey-band"></div>
<h2 class="abs section-title" style="left:76px;top:1304px">About Corvina Insurance Group</h2>
<p class="abs copy" style="left:76px;top:1349px;width:690px;line-height:26px">Established in 2015, Corvina Insurance Group is a full service independent insurance agency. Our licensed agents have the experience to custom tailor a program to meet your specific needs &amp; our professional support staff will provide you with top notch customer service to help ease the burden of managing your insurance program. We have established relationships with carriers in order to offer you the most competitive products and services available in the marketplace today.</p>
<p class="abs tagline">We look forward to working with you!</p>
<div class="abs btn-dark" style="left:76px;top:1591px">Read More</div>

<h2 class="abs section-title" style="left:795px;width:329px;text-align:center;top:1304px">Agents</h2>
<div class="abs agent-card">
  <div class="agent-photo" role="img" aria-label="Portrait photo of the agent"></div>
  <div class="agent-name">EVAN</div>
  <div class="agent-role">( Corvina Insurance Group Agent )</div>
  <div class="agent-desc">Vestibulum ante ipsum primis in faucibus orci luctus</div>
</div>

<section class="abs mission">
  <h2>Corvina Insurance Group Mission Statement</h2>
  <p>“Corvina Insurance Group is committed to providing the best risk management solutions to fit each client’s unique needs.<br>This includes providing creative solutions as if we were seeking insurance for our own family.”</p>
</section>

<!-- products -->
<h2 class="abs section-title" style="left:72px;top:1890px">Products and Services</h2>
<p class="abs copy" style="left:76px;top:1939px;width:430px;line-height:26px">Corvina Insurance Group is a one stop shop for all of your personal and business insurance needs. With our established relationships and market knowledge, we will tailor an insurance program specifically designed to meet your needs.</p>
<div class="abs btn-dark" style="left:76px;top:2086px">Read More</div>
<div class="abs tile business" style="left:524px"><div class="tile-bg" role="img" aria-label="Photo of hands holding a paper umbrella over a briefcase"></div><span>Business<br>Insurance</span></div>
<div class="abs tile personal" style="left:833px"><div class="tile-bg" role="img" aria-label="Photo of hands holding paper cutouts of a house, car and family"></div><span>Personal<br>Insurance</span></div>

<!-- footer -->
<svg class="abs footer-curve" viewBox="0 0 1200 112" aria-hidden="true">
  <path d="M0 22 C400 95 800 100 1200 28 L1200 112 L0 112 Z" fill="#2e7d3e"/>
  <path d="M0 78 C400 118 800 118 1200 62 L1200 112 L0 112 Z" fill="#333333"/>
  <path d="M30 0 C400 62 800 82 1200 18 L1200 40 C800 102 400 82 30 0 Z" fill="#1c3c6e"/>
</svg>
<footer>
  <div class="abs footer"></div>
  <div class="abs f-logo">CORVINA</div>
  <div class="abs f-copy">Copyright © 2016. Corvina Insurance Group<br>All Right Reserved | Terms Of Services</div>
  <div class="abs social bottom"><span></span><span></span><span></span><span></span></div>
  <div class="abs f-col" style="left:405px">
    <h4>Quick Links</h4>
    Home<br>About Us<br>Products and Services<br>Our Mission<br>Request Quote<br>Contact Us
  </div>
  <div class="abs f-col" style="left:615px">
    <h4>Contact Info</h4>
    <span class="brand">Corvina Insurance Group</span><br>
    <span style="display:block;line-height:20px;margin:3px 0 10px">1280 Harbor Lane, Suite 300<br>Baymont, FL 30100</span>
    Phone: (555) 010-2210<br>
    <span style="display:block;margin-top:4px">Fax: (555) 010-2211</span>
  </div>
  <div class="abs f-col" style="left:884px"><h4>Newsletter Sign Up</h4></div>
  <div class="abs f-input">Enter Email</div>
  <div class="abs f-btn">SIGN UP</div>
</footer>

</body>
</html>
```